Law Offices business card

Hi there, I'll need business card for the Law Offices of Colin Matheny. The information must convey his strategic approach and quick resolution to complex business litigation needs. Please emphasize Civil Litigation, Corporate Law, Business Governance and Real Estate Law. Colin has over 25 years of experience in these fields.The card should be modern and edgy and the message should be clear. Please consult his current website for ideas.

```html
<!DOCTYPE html>
<html lang="en">
<head>
<meta charset="utf-8">
<title>Law Offices of Colin Matheny – Business Card</title>
<link href="https://fonts.googleapis.com/css2?family=Tinos&family=Open+Sans:wght@400&family=Questrial&display=swap" rel="stylesheet">
<style>
  :root {
    --backdrop: #e9e6e1;
    --card: #f7f7f7;
    --ink: #141414;
    --band: #050505;
    --band-edge: #8c8c8c;
    --rule: #222222;
    --on-dark: #ffffff;
    --bullet: #555555;
  }
  html, body {
    margin: 0;
    width: 1200px;
    height: 892px;
    overflow: hidden;
    background: var(--backdrop);
  }
  .canvas {
    position: relative;
    width: 1200px;
    height: 892px;
  }
  .card {
    position: absolute;
    left: 265px;
    width: 670px;
    height: 383px;
    background: var(--card);
    box-shadow: 0 4px 14px rgba(0,0,0,0.18);
    overflow: hidden;
  }
  .card-front { top: 36px; }
  .card-back  { top: 473px; }
  .card svg { display: block; }
  .serif { font-family: "Tinos", "Times New Roman", serif; }
  .sans  { font-family: "Open Sans", Arial, sans-serif; }

  .back-heading {
    position: absolute;
    left: 78px;
    top: 22px;
    margin: 0;
    font-family: "Tinos", "Times New Roman", serif;
    font-weight: 400;
    font-size: 46px;
    color: var(--ink);
  }
  .back-rule {
    position: absolute;
    left: 0;
    right: 0;
    top: 88px;
    height: 2px;
    background: var(--rule);
  }
  .service-list {
    position: absolute;
    left: 70px;
    top: 142px;
    margin: 0;
    padding: 0;
    list-style: none;
    font-family: "Questrial", "Century Gothic", sans-serif;
    font-size: 28px;
    color: var(--ink);
    letter-spacing: 0.5px;
  }
  .service-list li {
    display: flex;
    align-items: center;
    gap: 22px;
    height: 54px;
  }
  .service-list svg { flex: none; }
</style>
</head>
<body>
<div class="canvas">

  <section class="card card-front">
    <svg width="670" height="383" viewBox="0 0 670 383">
      <path class="band-edge" d="M0,150 C200,150 330,200 420,270 C490,325 560,365 625,383 L0,383 Z" fill="var(--band-edge)"/>
      <path class="band" d="M0,168 C190,168 310,220 390,285 C450,335 520,368 580,383 L0,383 Z" fill="var(--band)"/>

      <text x="640" y="66" text-anchor="end" class="serif" font-size="32" fill="var(--ink)">Colin Matheny</text>
      <text x="622" y="90" text-anchor="end" class="sans" font-size="15" fill="var(--ink)">Attorney</text>
      <text x="640" y="134" text-anchor="end" class="serif" font-size="34" fill="var(--ink)">Law offices of Colin Matheny,P.A.</text>

      <g class="sans" font-size="16" fill="var(--on-dark)" text-anchor="end">
        <text x="286" y="256">561-555-0142</text>
        <text x="308" y="284">561-555-0187</text>
        <text x="330" y="312">www.mathenylaw.com</text>
        <text x="352" y="340">colin@mathenylaw.com</text>
        <text x="374" y="368">118B Harbor Avenue Palm Cove,Florida 33412</text>
      </g>
      <g fill="var(--on-dark)">
        <rect x="293" y="242" width="17" height="17" rx="2"/>
        <rect x="315" y="270" width="17" height="17" rx="2"/>
        <rect x="337" y="298" width="17" height="17" rx="2"/>
        <rect x="359" y="326" width="17" height="17" rx="2"/>
        <rect x="381" y="354" width="17" height="17" rx="2"/>
      </g>
      <g fill="none" stroke="var(--band)" stroke-width="1.5">
        <path d="M297,247 q5,-3 9,0 v2 h-3 l-1,-1 h-1 l-1,1 h-3 z M298,250 h7 v5 h-7 z"/>
        <rect x="320" y="273" width="7" height="11" rx="1"/>
        <circle cx="345.5" cy="306.5" r="5"/>
        <path d="M340.5,306.5 h10 M345.5,301.5 q-3,5 0,10 q3,-5 0,-10"/>
        <rect x="362.5" y="330.5" width="10" height="8"/>
        <path d="M362.5,330.5 l5,4 l5,-4"/>
        <path d="M389.5,367 l-4,-6 a4,4 0 1 1 8,0 z"/>
      </g>
    </svg>
  </section>

  <section class="card card-back">
    <h2 class="back-heading">Service</h2>
    <div class="back-rule"></div>
    <ul class="service-list">
      <li><svg width="16" height="16" viewBox="0 0 16 16"><circle cx="8" cy="8" r="5" fill="none" stroke="var(--bullet)" stroke-width="1.3"/><circle cx="8" cy="8" r="2" fill="var(--bullet)"/><path d="M8,0v3M8,13v3M0,8h3M13,8h3" stroke="var(--bullet)" stroke-width="1"/></svg>Civil Litigation</li>
      <li><svg width="16" height="16" viewBox="0 0 16 16"><circle cx="8" cy="8" r="5" fill="none" stroke="var(--bullet)" stroke-width="1.3"/><circle cx="8" cy="8" r="2" fill="var(--bullet)"/><path d="M8,0v3M8,13v3M0,8h3M13,8h3" stroke="var(--bullet)" stroke-width="1"/></svg>Corporate Law</li>
      <li><svg width="16" height="16" viewBox="0 0 16 16"><circle cx="8" cy="8" r="5" fill="none" stroke="var(--bullet)" stroke-width="1.3"/><circle cx="8" cy="8" r="2" fill="var(--bullet)"/><path d="M8,0v3M8,13v3M0,8h3M13,8h3" stroke="var(--bullet)" stroke-width="1"/></svg>Real Estate Law</li>
      <li><svg width="16" height="16" viewBox="0 0 16 16"><circle cx="8" cy="8" r="5" fill="none" stroke="var(--bullet)" stroke-width="1.3"/><circle cx="8" cy="8" r="2" fill="var(--bullet)"/><path d="M8,0v3M8,13v3M0,8h3M13,8h3" stroke="var(--bullet)" stroke-width="1"/></svg>Business Governance</li>
    </ul>
  </section>

</div>
</body>
</html>
```